Kesso Tea Premium Matcha brand Label

This is a label design project for a luxury tea brand. Feel free to be creative within the guidelines.
Attached to this project is a document called “Private Label Design Requirements” with the design guidelines and template. There is another document called "Kesso Tea Packaging Instructions" this has more details necessary to stick to the guidelines in the first document.

I have also attached the certifications to be included as well as different variations of the logo for you to use.

If you have any questions, I am here.
Updates

Need extra days to review

Target Market(s)

Young, active, fun, enjoy the finer things

```html
<!DOCTYPE html>
<html lang="en">
<head>
<meta charset="utf-8">
<title>Kesso Tea – Premium Organic Ceremonial Matcha Label</title>
<link href="https://fonts.googleapis.com/css2?family=Comfortaa:wght@400;500;700&display=swap" rel="stylesheet">
<style>
  :root{
    --page:#e4e4e4;
    --green:#019535;
    --green-deep:#0b5a24;
    --black:#040805;
    --kraft:#e3dacb;
    --brown:#8a4a12;
    --gold:#d4a84e;
    --gold-light:#f3dc9a;
    --title-green:#3fbf3a;
    --ink-dark:#3b3a36;
    --ink-light:#f4f4ef;
    --badge-blue:#2a78b8;
  }
  *{margin:0;padding:0;box-sizing:border-box}
  html,body{width:1200px;height:529px;overflow:hidden;background:var(--page)}
  body{font-family:"Comfortaa",sans-serif}
  .canvas{position:relative;width:1200px;height:529px;background:var(--page)}
  .label{position:absolute;left:20px;top:148px;width:1160px;height:233px}
  .label-art{position:absolute;inset:0;width:100%;height:100%}
  .label-text{position:absolute;white-space:nowrap}
  .brand-name{left:582px;top:101px;transform:translateX(-50%);font-size:17px;font-weight:700;color:var(--gold)}
  .distribution{left:59px;top:128px;font-size:13px;line-height:16px;color:var(--ink-light)}
  .distribution p{margin-bottom:4px}
  .distribution p.spaced{margin-top:5px}
  .cert-badge{position:absolute;left:62px;top:76px;width:58px;height:44px;border-radius:2px;background:var(--badge-blue)}
  .product-title{left:588px;top:154px;transform:translateX(-50%);font-size:25px;font-weight:500;color:var(--title-green);letter-spacing:.2px}
  .net-weight{left:588px;top:189px;transform:translateX(-50%);font-size:11.5px;color:var(--gold)}
  .instructions{right:67px;top:61px;text-align:right;font-size:13px;line-height:16.3px}
  .instructions .on-kraft{color:var(--ink-dark)}
  .instructions .on-green{color:var(--ink-light)}
  .storage{right:67px;top:176px;text-align:right;font-size:10.5px;line-height:14px;color:var(--ink-light);text-transform:uppercase}
  .organic-seal{position:absolute;left:940px;top:175px;width:28px;height:28px;border-radius:50%;background:#fff;border:3px solid var(--green-deep)}
</style>
</head>
<body>
<div class="canvas">
  <div class="label">
    <svg class="label-art" viewBox="0 0 1160 233" xmlns="http://www.w3.org/2000/svg" aria-hidden="false">
      <defs>
        <linearGradient id="bandShade" x1="0" x2="1" y1="0" y2="0">
          <stop offset="0" stop-color="#019535"/>
          <stop offset=".25" stop-color="#018a32"/>
          <stop offset=".4" stop-color="#031c0b"/>
          <stop offset=".5" stop-color="#040805"/>
          <stop offset=".6" stop-color="#031c0b"/>
          <stop offset=".75" stop-color="#018a32"/>
          <stop offset="1" stop-color="#019535"/>
        </linearGradient>
        <linearGradient id="bottomShade" x1="0" x2="1" y1="0" y2="0">
          <stop offset="0" stop-color="#019535"/>
          <stop offset=".2" stop-color="#018a32"/>
          <stop offset=".35" stop-color="#040805"/>
          <stop offset=".68" stop-color="#040805"/>
          <stop offset=".82" stop-color="#018a32"/>
          <stop offset="1" stop-color="#019535"/>
        </linearGradient>
        <linearGradient id="goldLine" x1="0" x2="1">
          <stop offset="0" stop-color="#8a4a12"/>
          <stop offset=".5" stop-color="#f3dc9a"/>
          <stop offset="1" stop-color="#8a4a12"/>
        </linearGradient>
        <radialGradient id="leafWash" cx=".5" cy=".55" r=".55">
          <stop offset="0" stop-color="#6fbf74" stop-opacity=".75"/>
          <stop offset="1" stop-color="#6fbf74" stop-opacity="0"/>
        </radialGradient>
      </defs>

      <rect class="top-band" x="0" y="0" width="1160" height="47" fill="url(#bandShade)"/>
      <rect class="rule-band" x="0" y="47" width="1160" height="7" fill="var(--brown)"/>
      <rect class="kraft-band" x="0" y="54" width="1160" height="72" fill="var(--kraft)"/>

      <g role="img" aria-label="Watercolour tea leaves, left">
        <ellipse cx="360" cy="92" rx="120" ry="42" fill="url(#leafWash)"/>
      </g>
      <g role="img" aria-label="Watercolour tea leaves, right">
        <ellipse cx="800" cy="92" rx="120" ry="42" fill="url(#leafWash)"/>
      </g>

      <rect class="bottom-band" x="0" y="126" width="1160" height="107" fill="url(#bottomShade)"/>

      <path class="centre-dip" d="M391 47 C470 47 500 150 582 150 C664 150 694 47 773 47 Z" fill="var(--black)"/>
      <path class="centre-dip-edge" d="M391 50 C470 50 500 150 582 150 C664 150 694 50 773 50" fill="none" stroke="url(#goldLine)" stroke-width="3"/>

      <circle class="brand-dot" cx="582" cy="80" r="11" fill="var(--gold)"/>

      <line x1="400" y1="196" x2="530" y2="196" stroke="url(#goldLine)" stroke-width="1"/>
      <line x1="634" y1="196" x2="764" y2="196" stroke="url(#goldLine)" stroke-width="1"/>
    </svg>

    <div class="label-text brand-name">Kesso Tea</div>

    <div class="cert-badge" role="img" aria-label="Non-GMO verification badge"></div>

    <div class="label-text distribution">
      <p>Distributed by Kesso Tea Co.|<br>Marlow, Ga</p>
      <p class="spaced">Certified Organic by veoa</p>
      <p>Product of Japan</p>
    </div>

    <div class="label-text product-title">Premium Organic Ceremonial Matcha</div>
    <div class="label-text net-weight">Net Wt: 30 g</div>

    <div class="label-text instructions">
      <div class="on-kraft">Premium Organic Japanese</div>
      <div class="on-kraft">Matcha Green Tea</div>
      <div class="on-kraft">Instructions</div>
      <div class="on-kraft">2 tsp of Matcha</div>
      <div class="on-green">2oz of Water (170-180 degrees F)</div>
      <div class="on-green">Whisk in a W formation until frothy</div>
      <div class="on-green">Sweeten to taste</div>
    </div>

    <div class="organic-seal" role="img" aria-label="Organic certification seal"></div>
    <div class="label-text storage">Keep refrigerated<br>for quality</div>
  </div>
</div>
</body>
</html>
```